USA Home and Kitchen "Multi-Product" Brand Needs a Stunning Packaging Design.

We need a new packaging design for our Brand: T&M Hearth & Dwelling. We Manufacture, Market, and Sell Home & Kitchen Products (Such as Kitchen Utensils and Home Decor to name a few) Direct to Consumers in the United States via our Website and Vendorly.com. We would like to see designs that are simple, clean, and modern, yet stand out and demand attention. Our Preferred colors of the design should include: Black or Grey as the base color/shade), White or Grey for the text, and some additional color can be used for complementary elements/visuals at your own discretion or creativity. We would like this to be an Interchangeable Design that can be easily modified and implemented across all of our other products (i.e: does not contain too many images or design elements that reference a particular product.

Although this design and the concept as a whole is intended to be used across our entire catalogue of products. Please feel free to base your design on our one of our top selling products as per the following URL: https://www.vendorly-example.com/dp/X93QL7714R?ref=abc_title_dp.

Target Market(s)

Our customers tend come from many areas across the spectrum. But the quintessential T&M target customer (the type of person who tends to be our most receptive and loyal customer) is female and part of the Millennials generation, aged in her 30s, and is either working full-time in a white-collar job or on home duties, of which she would have young children, a spouse, or other family members to look after. She’s part of the conventional family life who represent the core of ‘middle America’. She doesn’t mind to splurge every now and again on shopping for items that she wants and/or needs, whilst some of the time she’ll also go out of her way to ‘search for a bargain’. She tends to spend more time in her home and kitchen than the average individual. We recognize that cooking for herself and family, and providing a well furnished and stylish home is part of who she is.

Industry/Entity Type

Retail

Font styles to use
Serif
Sans Serif

Colors

Designer to choose only greyscale colors for use in the design.

Requirements
Must have
• Interchangeable Design (A "Universal" Packaging Design that can be easily modified and adapted for use with a large catalogue of products under our brand).
Nice to have
• Some visual elements that gives our packaging/brand the ability to stand out and be unique/memorable.
Should not have
• Our design should not have too much text. Nor should it be cluttered or overcrowded with too much information or visual elements. And does not contain too many images or design elements that reference a particular product. We believe simplicity is key, and quality over quantity.

```html
<!DOCTYPE html>
<html lang="en">
<head>
<meta charset="utf-8">
<title>T&amp;M Hearth &amp; Dwelling — Pie Server Packaging</title>
<link rel="stylesheet" href="https://fonts.googleapis.com/css2?family=Montserrat:wght@500;800&display=swap">
<style>
  :root {
    --bg: #e2e2e2;
    --panel-front: #0b0b0b;
    --panel-side: #050505;
    --text-white: #ffffff;
    --text-grey: #c9c9c9;
    --pattern-light: #f2f2f2;
    --pattern-mid: #bdbdbd;
  }
  html, body {
    margin: 0;
    padding: 0;
    width: 1200px;
    height: 789px;
    overflow: hidden;
    background: var(--bg);
  }
  .canvas {
    position: relative;
    width: 1200px;
    height: 789px;
    display: flex;
    justify-content: center;
    align-items: center;
  }
  .box-net {
    display: flex;
    height: 700px;
    box-shadow: 0 10px 30px rgba(0,0,0,0.18);
  }
  .panel {
    position: relative;
    height: 100%;
    font-family: "Montserrat", sans-serif;
    overflow: hidden;
  }
  .panel--side {
    width: 130px;
    background: var(--panel-side);
  }
  .panel--front {
    width: 262px;
    background: var(--panel-front);
  }
  .brand {
    position: absolute;
    left: 0;
    right: 0;
    text-align: center;
    color: var(--text-white);
    font-weight: 500;
    line-height: 1.1;
  }
  .panel--front .brand { top: 54px; }
  .panel--side .brand { top: 50px; color: var(--text-grey); }
  .brand__initials { display: block; font-size: 52px; letter-spacing: 1px; }
  .brand__name { display: block; font-size: 9px; letter-spacing: 1.5px; text-transform: uppercase; margin-top: 6px; }
  .panel--side .brand__initials { font-size: 22px; }
  .panel--side .brand__name { font-size: 5px; letter-spacing: 0.8px; margin-top: 3px; }
  .product {
    position: absolute;
    top: 262px;
    left: 0;
    right: 0;
    text-align: center;
    color: var(--text-white);
  }
  .product__title {
    margin: 0;
    font-weight: 800;
    font-size: 38px;
    line-height: 1.02;
    letter-spacing: 0.5px;
  }
  .product__tagline {
    margin: 10px 0 0;
    font-weight: 800;
    font-size: 9.5px;
    letter-spacing: 0.4px;
  }
  .side-title {
    position: absolute;
    top: 250px;
    left: 50%;
    transform: translateX(-50%) rotate(90deg);
    transform-origin: center;
    white-space: nowrap;
    margin: 0;
    color: var(--text-grey);
    font-weight: 800;
    font-size: 26px;
    line-height: 1;
    text-align: left;
    width: 150px;
    margin-left: 0;
  }
  .side-title span { display: block; }
  .pattern-band {
    position: absolute;
    left: 0;
    right: 0;
    bottom: 0;
    height: 205px;
  }
  .panel--front .pattern-band {
    background: radial-gradient(circle at 60% 40%, var(--pattern-light) 0%, #8a8a8a 55%, var(--panel-front) 100%);
  }
  .panel--side .pattern-band {
    height: 225px;
    background: radial-gradient(circle at 50% 40%, var(--pattern-mid) 0%, #5a5a5a 60%, var(--panel-side) 100%);
  }
</style>
</head>
<body>
  <main class="canvas">
    <div class="box-net">
      <section class="panel panel--side">
        <div class="brand">
          <span class="brand__initials">T&amp;M</span>
          <span class="brand__name">Hearth &amp; Dwelling</span>
        </div>
        <h2 class="side-title"><span>PIE</span><span>SERVER</span></h2>
        <div class="pattern-band" role="img" aria-label="Decorative honeycomb pattern of grey hexagons on black"></div>
      </section>
      <section class="panel panel--front">
        <div class="brand">
          <span class="brand__initials">T&amp;M</span>
          <span class="brand__name">Hearth &amp; Dwelling</span>
        </div>
        <div class="product">
          <h1 class="product__title">PIE<br>SERVER</h1>
          <p class="product__tagline">CUT AND SERVE SPATULA</p>
        </div>
        <div class="pattern-band" role="img" aria-label="Decorative honeycomb pattern of white hexagons on black"></div>
      </section>
    </div>
  </main>
</body>
</html>
```